Buch-/eBook-Cover für Anti-Stress-Adventskalender
TR Verlagshaus suchte ein neues Design in der Kategorie Buch-/eBook-Cover und hat ein Projekt auf grafikwerkstatt-online.de gestartet.
Zielgruppe
Wir sind als Selfpublisher vorwiegend bei Larvo Druckdienst aktiv und veröffentlichen Taschenbücher im Bereich Sachbücher, Ratgeber und Kinderbücher. Die Zielgruppe ist bei diesem Projekt schwieriger zu bestimmten, aber wird vsl. im Bereich der jungen Erwachsenen liegen und tendenziell eher im weiblichen Publikum.
Aufgabenstellung
Das Design sollte ein individuell auf das Projekt und auf die Zielgruppe abgestimmtes Konzept verfolgen, welches auf Larvo in die Augen sticht und Besteller Potential hat. Es sollte sich an bereits vorhanden Bestsellern in der jeweiligen Nische orientieren und dabei trotzdem die eigene Idee verdeutlichen. Der Sarkasmus und Humor des Buches und des Haupttitels sollte aus dem Cover hervorgehen.
Der Haupttitel: 17 Gründe, den Osterhasen trotzdem zu mögen
Der Nebentitel: Dein heiterer Entspannungs-Wochenplaner mit schrägen Geschichten, Knobeleien und bunten Übungen.
Autor: Jonas Riedl
Die Maße des Taschenbuchs werden wie folgt sein: 15.24 x 0.64 x 22.86 cm

```html
<!DOCTYPE html>
<html lang="de">
<head>
<meta charset="utf-8">
<title>17 Gründe, den Osterhasen trotzdem zu mögen – Cover</title>
<link rel="stylesheet" href="https://fonts.googleapis.com/css2?family=Luckiest+Guy&family=Patrick+Hand+SC&family=Poppins:wght@600;700&display=swap">
<style>
  :root{
    --stage:#c9c9c9;
    --red-deep:#a3202a;
    --red:#c8161f;
    --red-bright:#e31e24;
    --yellow:#f2d43a;
    --ink:#6b1a1e;
    --snow:#f7f3f2;
    --white:#ffffff;
    --display:"Luckiest Guy","Arial Black",Impact,sans-serif;
    --hand:"Patrick Hand SC","Comic Sans MS",sans-serif;
    --body:"Poppins",Arial,sans-serif;
  }
  *{box-sizing:border-box;margin:0;padding:0}
  html,body{width:672px;height:1200px;overflow:hidden;background:var(--stage)}
  .canvas{position:relative;width:672px;height:1200px}

  /* front cover component: 30em x 45em */
  .cover{position:relative;width:30em;height:45em;overflow:hidden;
    background:linear-gradient(165deg,var(--red-deep) 0%,var(--red) 45%,var(--red-bright) 100%);
    font-family:var(--display)}
  .cover--hero{position:absolute;font-size:14px;left:126px;top:22px;box-shadow:0 14px 30px rgba(0,0,0,.25)}
  .cover--spread{font-size:10px}

  .snow{position:absolute;inset:0;width:100%;height:100%}

  .title-block{position:absolute;left:1.3em;right:1.1em;top:1.2em}
  .title-row{display:flex;align-items:flex-end;gap:.5em;white-space:nowrap}
  .title-number{font-size:7.4em;line-height:.9;color:var(--yellow);text-shadow:.04em .04em 0 var(--ink)}
  .title-word{font-size:4em;line-height:1;color:var(--white);text-shadow:.05em .05em 0 var(--ink);padding-bottom:.08em}
  .title-line{display:block;margin-top:.35em;font-size:2.35em;line-height:1.1;color:var(--white);
    text-shadow:.06em .06em 0 var(--ink);white-space:nowrap}
  .title-highlight{display:inline-block;background:var(--yellow);color:var(--ink);padding:.1em .18em 0;
    text-shadow:none;margin-right:.2em;transform:rotate(-2deg)}

  .title-arrow{position:absolute;left:11em;top:16.2em;width:8em;height:2.8em}

  .subtitle{position:absolute;right:1.3em;top:19.2em;text-align:right;font-family:var(--hand);
    color:var(--white);line-height:1;text-shadow:.05em .05em 0 var(--ink)}
  .subtitle span{display:block}
  .subtitle .sub-small{font-size:1.7em}
  .subtitle .sub-big{font-size:2.4em;color:var(--yellow)}

  .hill{position:absolute;left:0;bottom:0;width:100%;height:15em}
  .illustration{position:absolute;left:.6em;top:19.5em;width:18em;height:23em;border-radius:48% 52% 40% 45%;
    background:radial-gradient(circle at 55% 38%,#f4e6df 0 22%,#d92a2f 23% 68%,rgba(200,22,31,0) 70%)}
  .author{position:absolute;right:1.3em;bottom:1.2em;font-size:2.3em;color:var(--red-bright);line-height:1}

  /* flat spread */
  .spread{position:absolute;left:26px;top:690px;width:620px;height:450px;display:flex;
    box-shadow:0 10px 24px rgba(0,0,0,.22)}
  .back-cover{position:relative;width:300px;height:450px;overflow:hidden;
    background:linear-gradient(175deg,var(--red-deep) 0%,var(--red) 45%,var(--red-bright) 100%)}
  .back-heading{position:absolute;left:0;right:0;top:40px;text-align:center;font-family:var(--hand);
    color:var(--white);line-height:1;text-shadow:1px 1px 0 var(--ink);font-weight:400}
  .back-heading .bh-small{display:block;font-size:14px}
  .back-heading .bh-big{display:block;font-size:25px;color:var(--yellow);margin-top:3px}
  .back-heading .bh-note{display:block;font-size:11px;margin-top:8px;line-height:1.15}
  .back-blurb{position:absolute;left:27px;width:246px;top:132px;font-family:var(--body);font-weight:600;
    font-size:6.4px;line-height:1.4;color:var(--white)}
  .back-landscape{position:absolute;left:0;top:240px;width:300px;height:130px}
  .back-illustration{position:absolute;left:6px;bottom:14px;width:150px;height:170px;border-radius:50%;
    background:radial-gradient(circle at 52% 35%,#f4e6df 0 22%,#b81a22 23% 66%,rgba(200,22,31,0) 68%)}

  .spine{position:relative;width:20px;height:450px;
    background:linear-gradient(180deg,var(--red-bright) 0%,var(--red-bright) 80%,var(--snow) 80%)}
  .spine-text{position:absolute;left:50%;top:43%;transform:translate(-50%,-50%) rotate(180deg);
    writing-mode:vertical-rl;white-space:nowrap;font-family:var(--body);font-weight:700;font-size:7px;
    color:var(--white)}
  .spine-author{color:var(--yellow)}
</style>
</head>
<body>
<main class="canvas">

  <section class="cover cover--hero" aria-label="Vorderseite">
    <svg class="snow" viewBox="0 0 300 450" aria-hidden="true" fill="#fff">
      <circle cx="205" cy="20" r="2.5"/><circle cx="262" cy="30" r="2"/><circle cx="150" cy="135" r="2"/>
      <circle cx="280" cy="155" r="2.5"/><circle cx="230" cy="172" r="2"/><circle cx="195" cy="290" r="2.5"/>
      <circle cx="270" cy="270" r="2"/><circle cx="30" cy="270" r="2"/>
    </svg>
    <svg class="hill" viewBox="0 0 300 150" preserveAspectRatio="none" aria-hidden="true">
      <path d="M0 40 C60 30 90 60 150 52 S250 20 300 30" fill="none" stroke="#fff" stroke-width="1.5"/>
      <path d="M0 95 C80 70 180 100 300 62 L300 150 L0 150 Z" fill="#f7f3f2"/>
    </svg>
    <div class="illustration" role="img" aria-label="Fröhlich springende Comicfigur vor verschneiter Landschaft mit Häusern und Tannen"></div>
    <div class="title-block">
      <div class="title-row"><span class="title-number">17</span><span class="title-word">Gründe</span></div>
      <span class="title-line">Den Osterhasen</span>
      <span class="title-line"><span class="title-highlight">Trotzdem</span>zu mögen</span>
    </div>
    <svg class="title-arrow" viewBox="0 0 85 30" aria-hidden="true">
      <path d="M82 3 C70 20 45 24 10 17" fill="none" stroke="#fff" stroke-width="3" stroke-linecap="round"/>
      <path d="M17 10 L8 17 L16 25" fill="none" stroke="#fff" stroke-width="3" stroke-linecap="round" stroke-linejoin="round"/>
    </svg>
    <div class="subtitle">
      <span class="sub-small">Dein heiterer</span>
      <span class="sub-big">Entspannungs-</span>
      <span class="sub-small">Wochenplaner</span>
    </div>
    <div class="author">Jonas Riedl</div>
  </section>

  <section class="spread" aria-label="Umschlag komplett">
    <div class="back-cover">
      <svg class="snow" viewBox="0 0 300 450" aria-hidden="true" fill="#fff">
        <circle cx="62" cy="20" r="2.5"/><circle cx="126" cy="18" r="1.5"/><circle cx="26" cy="46" r="1.5"/>
        <circle cx="264" cy="108" r="2.5"/><circle cx="232" cy="115" r="1.5"/>
      </svg>
      <h2 class="back-heading">
        <span class="bh-small">Dein heiterer Entspannungs-</span>
        <span class="bh-big">Wochenplaner</span>
        <span class="bh-note">Mit schrägen Geschichten, Knobeleien<br>und bunten Übungen.</span>
      </h2>
      <p class="back-blurb">Dieses Buch begleitet dich durch sieben Tage voller kleiner Pausen. Jede Seite bringt eine schräge Geschichte, eine Knobelei oder eine bunte Übung, die dich zum Schmunzeln bringt. Du brauchst nur einen Stift, etwas Neugier und fünf Minuten Zeit. Ob im Zug, auf dem Sofa oder in der Mittagspause: Hier darfst du lachen, rätseln und den Alltag kurz vergessen. Die Aufgaben sind leicht, die Ideen frisch und der Humor garantiert. Schenk dir selbst ein wenig Ruhe oder überrasche einen lieben Menschen damit. Am Ende der Woche wartet eine kleine Belohnung auf dich.</p>
      <svg class="back-landscape" viewBox="0 0 300 130" aria-hidden="true">
        <path d="M0 80 C70 70 110 40 170 50 S260 20 300 30" fill="none" stroke="#fff" stroke-width="1.5"/>
        <path d="M60 125 C120 110 200 120 300 100" fill="none" stroke="#fff" stroke-width="1.5"/>
      </svg>
      <div class="back-illustration" role="img" aria-label="Springende Comicfigur vor gezeichneter Winterlandschaft mit Haus und Tannen"></div>
    </div>

    <div class="spine">
      <div class="spine-text">17 Gründe den Osterhasen trotzdem zu mögen &nbsp;|&nbsp; <span class="spine-author">Jonas Riedl</span></div>
    </div>

    <div class="cover cover--spread" aria-label="Vorderseite im Umschlag">
      <svg class="snow" viewBox="0 0 300 450" aria-hidden="true" fill="#fff">
        <circle cx="205" cy="20" r="2.5"/><circle cx="262" cy="30" r="2"/><circle cx="150" cy="135" r="2"/>
        <circle cx="280" cy="155" r="2.5"/><circle cx="230" cy="172" r="2"/><circle cx="195" cy="290" r="2.5"/>
        <circle cx="270" cy="270" r="2"/><circle cx="30" cy="270" r="2"/>
      </svg>
      <svg class="hill" viewBox="0 0 300 150" preserveAspectRatio="none" aria-hidden="true">
        <path d="M0 40 C60 30 90 60 150 52 S250 20 300 30" fill="none" stroke="#fff" stroke-width="1.5"/>
        <path d="M0 95 C80 70 180 100 300 62 L300 150 L0 150 Z" fill="#f7f3f2"/>
      </svg>
      <div class="illustration" role="img" aria-label="Fröhlich springende Comicfigur vor verschneiter Landschaft mit Häusern und Tannen"></div>
      <div class="title-block">
        <div class="title-row"><span class="title-number">17</span><span class="title-word">Gründe</span></div>
        <span class="title-line">Den Osterhasen</span>
        <span class="title-line"><span class="title-highlight">Trotzdem</span>zu mögen</span>
      </div>
      <svg class="title-arrow" viewBox="0 0 85 30" aria-hidden="true">
        <path d="M82 3 C70 20 45 24 10 17" fill="none" stroke="#fff" stroke-width="3" stroke-linecap="round"/>
        <path d="M17 10 L8 17 L16 25" fill="none" stroke="#fff" stroke-width="3" stroke-linecap="round" stroke-linejoin="round"/>
      </svg>
      <div class="subtitle">
        <span class="sub-small">Dein heiterer</span>
        <span class="sub-big">Entspannungs-</span>
        <span class="sub-small">Wochenplaner</span>
      </div>
      <div class="author">Jonas Riedl</div>
    </div>
  </section>

</main>
</body>
</html>
```